Buch-/eBook-Cover für Traumatherapeutin
Zielgruppe
Ich bin Traumatherapeutin und schreibe ein Buch zum Thema Trauma bearbeiten.
Meine Zielgruppe sucht Heilung, Genesung, Selbstliebe etc.
Aufgabenstellung
Buchcover
Bitte erstell mir ein modernes positives inspirierendes Buchcover mit dem
Titel: 'Morgenlicht NEU entdecken“
Untertitel: „Spüre den Mut der ganz in dir wohnt“
Dr. Mira Kessow
Ich hätte gerne ein modernes Buch, das entweder einen Bezug zum Thema Trauma hat oder aber einfach stylische Schriftzüge. Bin aber auch offen für andere Vorschläge.
Dunkelblau, weiß und türkis oder auch rosa mag ich ganz gerne. Wobei Dunkelblau, weiß und türkis meine Favoriten sind und mit rosa höchstens kleinere Akzente gesetzt werden sollten.
Das Buchcover soll modern sein und direkt ansprechen. Gerne eine originelle Lösung, oder etwas Besonderes, etwas das Tiefe ausdrückt, oder man mehrmals hinsehen muss um etwas zu erkennen oder etwas das mehr Interpretationsspielraum lässt.
Gerne auch viel weiß, zumindest heller und nicht zu dunkel. Stylish, aber nicht überfrachtet.
Schreib mich gerne an, wenn du Fragen hast.
Ich habe mal zwei Beispiel von Typolösungen angehängt, die ich ganz cool fände.
Ich freue mich auf deine Ideen :-)
Ganz liebe Grüße
Mira

```html
<!DOCTYPE html>
<html lang="de">
<head>
<meta charset="utf-8">
<title>Morgenlicht NEU entdecken – Buchcover</title>
<link href="https://fonts.googleapis.com/css2?family=Lobster&family=Oswald:wght@600&family=Josefin+Sans:wght@600;700&family=Kaushan+Script&display=swap" rel="stylesheet">
<style>
  :root {
    --stage: #e9ecee;
    --paper: #f1f1f1;
    --ink: #161616;
    --teal: #1dbab4;
    --teal-deep: #0f8f8a;
    --pink: #ef9a96;
    --red: #e8383a;
  }
  * { margin: 0; padding: 0; box-sizing: border-box; }
  html, body {
    width: 1200px;
    height: 960px;
    overflow: hidden;
    background: var(--stage);
  }
  .cover {
    position: absolute;
    left: 303px;
    top: 50px;
    width: 594px;
    height: 860px;
    background: var(--paper);
    overflow: hidden;
  }
  .author {
    position: absolute;
    top: 22px;
    width: 100%;
    text-align: center;
    font-family: "Josefin Sans", sans-serif;
    font-weight: 700;
    font-size: 33px;
    letter-spacing: 0.5px;
    color: var(--ink);
  }
  .title-script {
    position: absolute;
    width: 100%;
    text-align: center;
    font-family: "Lobster", cursive;
    color: var(--teal);
    text-shadow: 3px 4px 0 var(--teal-deep), 5px 7px 0 var(--teal-deep);
    transform: rotate(-3deg);
  }
  .title-top { top: 218px; font-size: 104px; letter-spacing: -1px; }
  .title-bottom { top: 482px; font-size: 106px; letter-spacing: -1px; }
  .title-accent {
    position: absolute;
    top: 368px;
    width: 100%;
    text-align: center;
    font-family: "Oswald", sans-serif;
    font-weight: 600;
    font-size: 104px;
    line-height: 1;
    letter-spacing: 2px;
    color: var(--pink);
    text-shadow: 5px 3px 0 var(--red);
  }
  .subtitle {
    position: absolute;
    top: 690px;
    width: 100%;
    text-align: center;
    font-family: "Josefin Sans", sans-serif;
    font-weight: 600;
    font-size: 28px;
    line-height: 38px;
    color: var(--ink);
    transform: rotate(-3deg);
  }
  .subtitle em {
    font-family: "Kaushan Script", cursive;
    font-style: normal;
    font-size: 30px;
  }
</style>
</head>
<body>
  <main class="cover">
    <p class="author">DR. MIRA KESSOW</p>
    <h1>
      <span class="title-script title-top">Morgenlicht</span>
      <span class="title-accent">NEU</span>
      <span class="title-script title-bottom">entdecken</span>
    </h1>
    <p class="subtitle">Spüre den <em>Mut</em><br>der ganz <em>in dir wohnt</em></p>
  </main>
</body>
</html>
```